Dusty Spur Outfitters Home Page

I need a logo and page design for my home page, maybe some background color suggestions to go with it. I want the logo to project "vintage" and "western wear" but not be your typical trite western saddle and gun type thing.
http://www.dustyspuroutfitters.example/store/cart.php
Not looking for page coding just logo and other design elements to lay in over the site's template to make it "pop"
Reason: Have to finalize the design.
Target Market(s)
My customers are 70/30 men to women.
Industry/Entity Type
Gun

```html
<!DOCTYPE html>
<html lang="en">
<head>
<meta charset="utf-8">
<title>Dusty Spur Outfitters</title>
<link rel="stylesheet" href="https://fonts.googleapis.com/css2?family=Oswald:wght@500&family=Rye&family=Lato:wght@400;700&display=swap">
<style>
  :root{
    --linen:#cbb998;
    --topbar:#dccfb6;
    --header:#2a2825;
    --header-edge:#4a4640;
    --ink:#2b2926;
    --cream:#e7d9bc;
    --teal:#3fa6b8;
    --field:#2e2c29;
    --search:#ece0c6;
    --frame:#e9dec7;
    --shirt:#86c2de;
    --shirt-dark:#6aaccd;
    --sky:#7fd3e8;
  }
  *{box-sizing:border-box;margin:0;padding:0}
  html,body{width:1200px;height:1012px;overflow:hidden}
  body{position:relative;background:var(--linen);font-family:"Lato",sans-serif;color:var(--ink)}
  .abs{position:absolute}

  .topbar{left:0;top:0;width:1200px;height:46px;background:var(--topbar)}
  .nav-link{position:absolute;top:9px;font-family:"Oswald",sans-serif;font-weight:500;font-size:20px;letter-spacing:.2px;color:var(--ink);white-space:nowrap;line-height:26px}
  .icon{position:absolute;top:10px}

  .header-shadow{left:0;top:46px;width:1200px;height:180px;background:linear-gradient(#a69a86,#9a8e7b 12px,transparent 12px)}
  .header{left:0;top:70px;width:1200px;height:132px;background:var(--header);box-shadow:0 12px 14px -4px rgba(40,36,30,.55),0 -8px 10px rgba(60,55,48,.35)}
  .header-edge{left:0;top:202px;width:1200px;height:20px;background:linear-gradient(rgba(74,70,64,.8),rgba(74,70,64,0))}

  .brand{left:58px;top:104px;display:flex;align-items:center;gap:14px}
  .brand-mark{width:22px;height:22px;border-radius:50%;background:var(--cream)}
  .brand-name{font-family:"Rye",serif;font-size:30px;color:var(--cream);white-space:nowrap}

  .tagline{left:500px;top:96px;width:372px;text-align:center;font-family:"Rye",serif;font-size:18px;line-height:21px;color:#d6c8aa}
  .subline{left:479px;top:156px;width:503px;font-family:"Rye",serif;font-size:17.5px;color:#d6c8aa;white-space:nowrap}

  .search{left:901px;top:107px;width:173px;height:30px;border-radius:15px;background:var(--search);font-weight:700;font-size:18px;padding:4px 0 0 17px;color:var(--ink)}
  .search-go{left:1084px;top:110px;font-weight:700;font-size:18px;color:#6f6a60}

  .side-title{font-family:"Rye",serif;color:var(--ink);white-space:nowrap}
  .msg{left:62px;top:262px;font-size:24px}
  .news{left:59px;top:330px;font-size:25px}
  .email{left:59px;top:373px;width:174px;height:30px;border-radius:15px;background:var(--field);color:var(--teal);font-weight:700;font-size:18px;padding:4px 0 0 17px}
  .email-go{left:242px;top:377px;color:var(--teal);font-weight:700;font-size:18px}

  .list-title{left:59px;font-size:19px}
  .side-list{left:58px;list-style:none;font-size:15.6px;line-height:19.7px;color:var(--ink)}

  .banner{left:371px;top:236px;width:768px;height:388px;background:var(--frame);padding:5px;box-shadow:0 2px 5px rgba(0,0,0,.35)}
  .banner-img{width:100%;height:100%;background:linear-gradient(160deg,#c9d4da 0%,#9ccbe3 30%,var(--shirt) 60%,var(--shirt-dark) 100%);position:relative}
  .banner-label{position:absolute;right:8px;top:262px;font-family:"Rye",serif;font-size:26px;color:#efe6d2;text-shadow:1px 2px 2px rgba(0,0,0,.55)}
  .dot{top:665px;width:11px;height:11px;border-radius:50%;border:2px solid var(--ink)}

  .featured{left:374px;top:738px;font-family:"Rye",serif;font-size:44px;color:var(--ink);white-space:nowrap}
  .product{top:836px;width:199px;height:190px;background:var(--frame);padding:5px;box-shadow:0 2px 5px rgba(0,0,0,.35)}
  .product-img{width:100%;height:100%}
</style>
</head>
<body>

<div class="abs topbar">
  <span class="nav-link" style="left:57px">MEN'S WESTERN WEAR</span>
  <span class="nav-link" style="left:257px">WOMEN'S WESTERN WEAR</span>
  <span class="nav-link" style="left:485px">NEW ARRIVALS!</span>
  <span class="nav-link" style="left:625px">BOOTS</span>
  <span class="nav-link" style="left:840px">SIZING CHARTS</span>
  <span class="nav-link" style="left:976px">HELP</span>
  <svg class="icon" style="left:1046px" width="30" height="26" viewBox="0 0 30 26" aria-label="Account">
    <circle cx="9" cy="7" r="5.5" fill="#2b2926"/>
    <path d="M0 22c0-7 4-9 9-9s9 2 9 9z" fill="#2b2926"/>
    <path d="M22 15l3.5 3.5 3.5-3.5" fill="none" stroke="#2b2926" stroke-width="2"/>
  </svg>
  <svg class="icon" style="left:1093px" width="48" height="26" viewBox="0 0 48 26" aria-label="Cart">
    <path d="M1 2h5l4 14h17l3-10H8" fill="none" stroke="#2b2926" stroke-width="3"/>
    <path d="M9 6h21l-3 10H11z" fill="#2b2926"/>
    <circle cx="12" cy="21" r="2.5" fill="#2b2926"/>
    <circle cx="25" cy="21" r="2.5" fill="#2b2926"/>
    <path d="M36 15l3.5 3.5 3.5-3.5" fill="none" stroke="#2b2926" stroke-width="2"/>
  </svg>
</div>

<div class="abs header-shadow"></div>
<div class="abs header"></div>
<div class="abs header-edge"></div>

<div class="abs brand">
  <span class="brand-mark"></span>
  <span class="brand-name">Dusty Spur Outfitters</span>
</div>

<p class="abs tagline">Internet's best selection and value<br>for brand new Retro-Styled</p>
<p class="abs subline">VINTAGE WESTERN FASHIONS FOR MEN AND WOMEN</p>

<div class="abs search">Search...</div>
<span class="abs search-go">GO!</span>

<h2 class="abs side-title msg">LEAVE US A MESSAGE!</h2>
<h2 class="abs side-title news">Join our Newsletter!</h2>
<div class="abs email">Email</div>
<span class="abs email-go">GO!</span>

<h3 class="abs side-title list-title" style="top:461px">CATEGORIES</h3>
<ul class="abs side-list" style="top:497px">
  <li>Men's Western Wear</li>
  <li>Women's Western Wear</li>
  <li>Boots</li>
  <li>Accessories</li>
  <li>Belts</li>
  <li>Big and tall</li>
  <li>Brand New Arrivals</li>
  <li>CLEARANCE</li>
  <li>Handbags</li>
  <li>Jackets</li>
  <li>Jeans</li>
  <li>Leather</li>
  <li>ON Sale</li>
  <li>Pants</li>
  <li>Short Sleeves</li>
  <li>T-Shirts</li>
  <li>Vests</li>
</ul>

<h3 class="abs side-title list-title" style="top:862px">INFORMATION</h3>
<ul class="abs side-list" style="top:897px">
  <li>About Us</li>
  <li>Contact Us</li>
  <li>Privacy Policy</li>
  <li>Shipping and Returns</li>
  <li>Sizing Charts</li>
</ul>

<div class="abs banner">
  <div class="banner-img" role="img" aria-label="Back of a light blue western shirt with dark embroidered scrollwork across the yoke">
    <span class="banner-label">NEW ARRIVALS</span>
  </div>
</div>
<span class="abs dot" style="left:735px"></span>
<span class="abs dot" style="left:763px;background:var(--ink)"></span>

<h2 class="abs featured">FEATURED PRODUCTS</h2>

<div class="abs product" style="left:397px">
  <div class="product-img" role="img" aria-label="Man wearing a black embroidered western shirt" style="background:linear-gradient(180deg,#6fd0ea 0%,#5cc3e0 45%,#2d3338 75%,#24292d 100%)"></div>
</div>
<div class="abs product" style="left:665px">
  <div class="product-img" role="img" aria-label="Man wearing a cream western shirt with light blue yoke" style="background:linear-gradient(180deg,#8fc8e6 0%,#86c0e0 45%,#cfe4ef 70%,#efe6d4 100%)"></div>
</div>
<div class="abs product" style="left:934px">
  <div class="product-img" role="img" aria-label="Man in a black hat wearing a burgundy vest over a white shirt" style="background:linear-gradient(180deg,#93dcf0 0%,#8ad6ee 45%,#d8cfc3 70%,#6a3532 100%)"></div>
</div>

</body>
</html>
```